Teach English in China Website Redesign Needed

We recruit native English speakers from the US, UK, etc. who want to teach English as a foreign language in schools in China. Our target customer is college educated, age 22-28 and they love to travel. We prefer designs with bright colors and lots of photos. We want to keep all the text on our current homepage, BrightLanternPost.com. We are open to changing our logo. A competitor's page that we like is pinemeadowtutors.com because of their bright colors, photos and use of white space. We are happy to give you a dofollow link and design credit on our homepage. The use of included photos is optional. We need at least a home page design and a standard blog post design.
Target Market(s)
Our target customer is college educated, age 22-28 and they love to travel. Half of our customers are kindergarten teachers. Half of our customers are male.
Logo Text
Bright Lantern Post
Requirements
Must have
- Bright colors
Should not have
- Our homepage must not look crowded. Use white space effectively.

```html
<!DOCTYPE html>
<html lang="en">
<head>
<meta charset="utf-8">
<title>Bright Lantern Post – Teach English in China</title>
<link rel="stylesheet" href="https://fonts.googleapis.com/css2?family=Open+Sans:wght@300;400;600;700&display=swap">
<style>
:root{
  --black:#000;
  --ink:#222;
  --text:#555;
  --muted:#888;
  --line:#ddd;
  --yellow:#ffd400;
  --gold:#f2b705;
  --white:#fff;
  --footer:#0b0b0b;
  --base:#262626;
}
*{box-sizing:border-box;margin:0;padding:0}
html,body{width:1200px;height:3201px;overflow:hidden;background:var(--white)}
body{position:relative;font-family:"Open Sans",Arial,sans-serif;color:var(--text)}
h1,h2,h3,h4{font-weight:400}
.abs{position:absolute}
a{color:inherit;text-decoration:none}

.top-bar{left:0;top:0;width:1200px;height:31px;background:var(--black)}
.top-links{left:42px;top:0;height:31px;display:flex;gap:30px;align-items:center;color:var(--white);font-size:12px;font-weight:700;letter-spacing:.3px}
.social-dots{right:50px;top:8px;display:flex;gap:4px}
.social-dots span{width:14px;height:14px;border-radius:50%;background:#777}

.header{left:0;top:31px;width:1200px;height:128px;background:var(--white);border-bottom:1px solid var(--line)}
.brand{left:44px;top:58px;height:75px;display:flex;align-items:center;gap:12px;font-size:30px;font-weight:700;color:var(--black);white-space:nowrap}
.brand i{width:22px;height:22px;background:var(--yellow);display:block}
.main-nav{left:575px;top:84px;display:flex;gap:22px;font-size:15px;color:var(--ink);font-weight:600}
.main-nav .active{border-bottom:2px solid var(--ink)}
.search{left:1124px;top:78px}

.hero{left:0;top:159px;width:1200px;height:549px;
  background:
    linear-gradient(180deg,rgba(255,255,255,0) 0%,rgba(255,255,255,0) 62%,rgba(40,60,80,.55) 72%,rgba(120,110,100,.35) 100%),
    radial-gradient(ellipse 420px 320px at 1120px 360px,rgba(255,190,90,.95),rgba(255,170,80,0) 70%),
    linear-gradient(100deg,#4f6f8c 0%,#7f9fbc 28%,#b4c3cf 50%,#d9c1a2 72%,#f3a65c 90%,#f8cf8d 100%)}
.hero-text{left:42px;top:448px;color:var(--white)}
.hero-text p{font-size:29px;font-weight:300}
.hero-text h1{font-size:46px;font-weight:400;letter-spacing:.5px;margin-top:2px}
.chev{width:30px;height:44px}

.intro-title{left:0;top:745px;width:1200px;text-align:center;font-size:34px;font-weight:400;color:var(--ink);letter-spacing:1px}
.avatar{left:73px;top:799px;width:124px;height:124px;border-radius:50%;background:radial-gradient(circle at 50% 40%,#e2c2a8,#a47252 60%,#6a4a35)}
.intro-copy{left:228px;top:826px;width:840px;font-size:12px;line-height:15.5px;letter-spacing:.2px;color:var(--muted)}
.intro-copy b{color:#444;font-weight:600}
.intro-copy p{margin-bottom:16px}
.intro-copy .wide{margin-left:-91px;width:931px}
.btn-tab{height:35px;background:var(--yellow);color:var(--white);font-size:11px;font-weight:700;display:flex;align-items:center;justify-content:center;letter-spacing:.5px}
.btn-tab::after{content:"";position:absolute;left:50%;bottom:-8px;margin-left:-8px;border:8px solid transparent;border-bottom:0;border-top-color:var(--yellow)}

.cities{left:0;top:1134px;width:1200px;height:172px;
  background:
    linear-gradient(180deg,rgba(255,255,255,0) 55%,rgba(60,70,60,.45) 100%),
    linear-gradient(90deg,#7d3a2a 0%,#b05a3e 10%,#c7d3de 26%,#d6e0e8 50%,#c7d3de 74%,#a0603f 90%,#6a3b2e 100%)}
.city-card{top:1140px;width:282px;height:160px;border:3px solid #333;color:var(--white);text-align:center;padding-top:36px;font-size:15px;font-weight:600}
.city-card small{display:block;font-size:13px;font-weight:400;margin-top:8px}

.blog-title{left:0;top:1340px;width:1200px;text-align:center;font-size:36px;color:var(--ink);font-weight:400}
.blog-lead{left:300px;top:1400px;width:600px;text-align:center;font-size:13px;line-height:20px;color:var(--muted)}
.post{top:1470px;width:288px}
.post .thumb{height:162px}
.post h3{font-size:14px;color:var(--ink);font-weight:700;margin-top:42px}
.post p{font-size:11.5px;line-height:16px;color:var(--muted);margin-top:12px}
.post .meta{font-size:11px;color:var(--gold);margin-top:12px}
.round-arrow{width:48px;height:56px;border-radius:50%;background:#c8c8c8;display:flex;align-items:center;justify-content:center}
.btn{background:var(--yellow);color:var(--white);font-weight:700;font-size:16px;display:flex;align-items:center;justify-content:center;letter-spacing:.5px}

.testimonials{left:0;top:1922px;width:1200px;height:529px;
  background:
    linear-gradient(180deg,rgba(255,255,255,0) 70%,rgba(190,195,200,.6) 100%),
    linear-gradient(180deg,#f7f7f7 0%,#eceef0 50%,#dcdfe3 100%)}
.t-title{left:0;top:1962px;width:1200px;text-align:center;font-size:32px;color:var(--ink);font-weight:400}
.t-avatar{left:534px;top:2072px;width:124px;height:124px;border-radius:50%;border:4px solid var(--white);background:radial-gradient(circle at 50% 40%,#d4a98b,#7a5040 60%,#3a2620)}
.quote{left:250px;top:2222px;width:700px;text-align:center;font-size:15px;line-height:22px;color:#666}
.qmark{font-size:90px;color:#b7b7b7;font-family:Georgia,serif;line-height:1}
.t-name{left:0;top:2310px;width:1200px;text-align:center;font-size:14px;color:var(--gold);font-weight:700}
.t-role{left:0;top:2338px;width:1200px;text-align:center;font-size:13px;color:#555}
.square-arrow{width:60px;height:60px;border-radius:10px;background:#bdbdbd;display:flex;align-items:center;justify-content:center}
.dots{left:352px;top:2406px;display:flex;gap:20px}
.dots span{width:18px;height:18px;border-radius:50%;border:2px solid #aaa}
.dots .on{background:var(--gold);border-color:var(--gold)}

.process-title{left:0;top:2462px;width:1200px;text-align:center;font-size:24px;font-weight:400;letter-spacing:1.5px;color:var(--ink)}
.step{top:2518px;width:160px;text-align:center}
.step .ring{width:116px;height:116px;border-radius:50%;border:4px solid var(--black);margin:0 auto;display:flex;align-items:center;justify-content:center;background:var(--white)}
.step span{display:block;margin-top:22px;font-size:16px;letter-spacing:1px;color:#555}

.cta{left:0;top:2739px;width:1200px;height:197px;
  background:
    linear-gradient(180deg,rgba(255,255,255,.15) 0%,rgba(120,125,130,.35) 100%),
    linear-gradient(90deg,#2c5fb0 0%,#5a7fb8 9%,#aab5c1 20%,#c4cad0 50%,#b7bec6 78%,#c9a58e 90%,#e2b899 100%)}

.footer{left:0;top:2936px;width:1200px;height:226px;background:var(--footer);color:#cfcfcf}
.f-col h4{font-size:12px;font-weight:700;color:var(--white);letter-spacing:1px;margin-bottom:18px}
.f-col p,.f-col li{font-size:10.5px;line-height:15px;list-style:none}
.f-brand{left:879px;top:3016px;width:193px;height:66px;padding:0 8px;background:#bdbdbd;color:var(--black);font-size:17px;font-weight:700;white-space:nowrap;display:flex;align-items:center;justify-content:center}
.base-bar{left:0;top:3162px;width:1200px;height:39px;background:var(--base);color:#888;font-size:11px}
</style>
</head>
<body>

<div class="abs top-bar"></div>
<nav class="abs top-links"><a>JOB BOARD</a><a>APPLY</a><a>BLOG</a><a>HIRE A TEACHER</a><a>ABOUT US</a></nav>
<div class="abs social-dots"><span></span><span></span><span></span><span></span><span></span><span></span></div>

<header class="abs header"></header>
<div class="abs brand"><i></i>Bright Lantern Post</div>
<nav class="abs main-nav"><a class="active">Home</a><a>Available Jobs</a><a>Apply Online</a><a>Blog</a><a>About</a><a>FAQ</a></nav>
<svg class="abs search" width="34" height="34" viewBox="0 0 34 34"><circle cx="14" cy="14" r="9" fill="none" stroke="#888" stroke-width="4"/><line x1="21" y1="21" x2="30" y2="30" stroke="#888" stroke-width="5" stroke-linecap="round"/></svg>

<section class="abs hero" role="img" aria-label="Photo of the Shanghai skyline across the river at sunset"></section>
<svg class="abs chev" style="left:20px;top:415px" viewBox="0 0 30 44"><polyline points="24,4 6,22 24,40" fill="none" stroke="#fff" stroke-width="3"/></svg>
<svg class="abs chev" style="left:1150px;top:415px" viewBox="0 0 30 44"><polyline points="6,4 24,22 6,40" fill="none" stroke="#fff" stroke-width="3"/></svg>
<div class="abs hero-text"><p>We will help you</p><h1>TEACH ENGLISH IN CHINA</h1></div>

<h2 class="abs intro-title">TEACH ENGLISH IN CHINA</h2>
<div class="abs avatar" role="img" aria-label="Portrait photo of the director"></div>
<div class="abs intro-copy">
  <p><b>Want to teach English in China?</b> Do you enjoy teaching children or adults? Would you like the adventure of teaching in China for a year? Then we have the perfect job for you! We are seeking English speakers from the US, UK, Canada, Ireland, Australia, New Zealand and South Africa to teach English in China for a year (or longer if you wish). We recruit for hundreds of schools all over China such as Northgate Language, Harbor Street Academy, Linden English, Copperfield English, Willow Bridge, Crestline Learning, Amber Orchard, public schools, international schools, universities, and more.</p>
  <p><b>Don't want to fly to China alone?</b><br>No problem, fly over with other new teachers and our American Director, Marla Fenwick. She'll help you get settled and adjusted to Chinese culture. We take EXCELLENT care of our teachers with ongoing American and local support for your entire year in China.</p>
  <p class="wide">A Bachelor's degree and experience is recommended, but a degree is not required to teach kindergarten. If you have a Bachelor's degree,<br>you also have the option to teach older children and adults. Also, more good news is that you do NOT need to know how to speak Chinese.<br>Also, we provide FREE TEFL / TESOL 120-hour online certification to all the teachers we place.</p>
</div>
<a class="abs btn-tab" style="left:480px;top:1065px;width:96px">VIEW MORE</a>
<a class="abs btn-tab" style="left:620px;top:1065px;width:93px">PROCESS</a>

<section class="abs cities" role="img" aria-label="Photo of traditional Chinese rooftops and mountains"></section>
<svg class="abs chev" style="left:20px;top:1196px" viewBox="0 0 30 44"><polyline points="24,4 6,22 24,40" fill="none" stroke="#fff" stroke-width="3"/></svg>
<svg class="abs chev" style="left:1150px;top:1196px" viewBox="0 0 30 44"><polyline points="6,4 24,22 6,40" fill="none" stroke="#fff" stroke-width="3"/></svg>
<div class="abs city-card" style="left:290px;background:linear-gradient(180deg,#8fa6bd 0%,#6d87a1 45%,#4d6176 75%,#8a97a4 100%)" role="img" aria-label="Photo of Shanghai city">TEACH IN SHANGHAI<small>Apply now!</small></div>
<div class="abs city-card" style="left:622px;background:linear-gradient(180deg,#b49a80 0%,#8d7663 45%,#5e5048 75%,#8d8478 100%)" role="img" aria-label="Photo of Shenzhen city">TEACH IN SHENZHEN<small>Apply now!</small></div>

<h2 class="abs blog-title">OUR BLOG</h2>
<p class="abs blog-lead">Lorem ipsum dolor sit amet, consectetur adipiscing elit. Nam odio magna, interdum vel neque nec, tempor sollicitudin lorem. Quisque at tincidunt odio.</p>
<div class="abs round-arrow" style="left:55px;top:1572px"><svg width="16" height="24" viewBox="0 0 16 24"><polyline points="12,3 4,12 12,21" fill="none" stroke="#fff" stroke-width="3"/></svg></div>
<div class="abs round-arrow" style="left:1094px;top:1572px"><svg width="16" height="24" viewBox="0 0 16 24"><polyline points="4,3 12,12 4,21" fill="none" stroke="#fff" stroke-width="3"/></svg></div>
<article class="abs post" style="left:144px">
  <div class="thumb" role="img" aria-label="Photo of a young child eating noodles" style="background:radial-gradient(ellipse at 40% 55%,#f0d2b4 0%,#d89a70 30%,rgba(200,60,40,0) 60%),linear-gradient(135deg,#7a3a24,#c4432c 50%,#e7c3a0)"></div>
  <h3>Lorem ipsum dolor sit amet</h3>
  <p>Lorem ipsum dolor sit amet, consectetur adipiscing elit, sed do eiusmod tempor incididunt ut labore et dolore magna aliqua. Ut enim ad minim veniam, quis</p>
  <div class="meta">09 Sep 2015 / By Admin / 0 Comments</div>
</article>
<article class="abs post" style="left:456px">
  <div class="thumb" role="img" aria-label="Photo of schoolchildren in uniforms" style="background:linear-gradient(180deg,#6fa058 0%,#8fb877 25%,#e9e3d6 50%,#d24a3a 78%,#3e3a6a 100%)"></div>
  <h3>Lorem ipsum dolor sit amet</h3>
  <p>Lorem ipsum dolor sit amet, consectetur adipiscing elit, sed do eiusmod tempor incididunt ut labore et dolore magna aliqua. Ut enim ad minim veniam, quis</p>
  <div class="meta">10 Sep 2015 / By Admin / 0 Comments</div>
</article>
<article class="abs post" style="left:768px">
  <div class="thumb" role="img" aria-label="Photo of a teacher with a group of students" style="background:radial-gradient(ellipse at 55% 45%,#b07a5a 0%,rgba(120,80,60,0) 55%),linear-gradient(135deg,#3a2e2a,#6e4c3c 45%,#2d6a9c 85%,#e0c070)"></div>
  <h3>Lorem ipsum dolor sit amet</h3>
  <p>Lorem ipsum dolor sit amet, consectetur adipiscing elit, sed do eiusmod tempor incididunt ut labore et dolore magna aliqua. Ut enim ad minim veniam, quis</p>
  <div class="meta">14 Sep 2015 / By Admin / 0 Comments</div>
</article>
<a class="abs btn" style="left:516px;top:1824px;width:159px;height:51px">VIEW MORE</a>

<section class="abs testimonials" role="img" aria-label="Faded photo of a city skyline"></section>
<h2 class="abs t-title">TESTIMONIALS</h2>
<div class="abs t-avatar" role="img" aria-label="Portrait photo of a teacher"></div>
<div class="abs square-arrow" style="left:51px;top:2154px"><svg width="18" height="28" viewBox="0 0 18 28"><polyline points="14,3 4,14 14,25" fill="none" stroke="#fff" stroke-width="3"/></svg></div>
<div class="abs square-arrow" style="left:1086px;top:2154px"><svg width="18" height="28" viewBox="0 0 18 28"><polyline points="4,3 14,14 4,25" fill="none" stroke="#fff" stroke-width="3"/></svg></div>
<span class="abs qmark" style="left:192px;top:2186px">&ldquo;</span>
<span class="abs qmark" style="left:960px;top:2220px">&rdquo;</span>
<p class="abs quote">ipsum dolor sit amet, consectetur adipiscing elit. Vestibulum ac tincidunt lacus. Pellentesque orci mauris, luctus non tortor sit amet pretium porta ipsum.</p>
<div class="abs t-name">Lorem ipsum</div>
<div class="abs t-role">Lorem ipsum dolor sit amet</div>
<div class="abs dots"><span></span><span class="on"></span><span></span><span></span><span></span><span></span><span></span><span></span><span></span><span></span><span></span><span></span><span></span></div>

<h2 class="abs process-title">PROCESS</h2>
<div class="abs step" style="left:46px"><div class="ring"><svg width="48" height="48" viewBox="0 0 48 48"><path d="M10 38 L13 28 L32 9 L39 16 L20 35 Z" fill="var(--yellow)"/><path d="M10 38 L13 28 L20 35 Z" fill="#e0a800"/></svg></div><span>APPLY</span></div>
<div class="abs step" style="left:234px"><div class="ring"><svg width="48" height="48" viewBox="0 0 48 48"><path d="M10 38 L13 28 L32 9 L39 16 L20 35 Z" fill="var(--yellow)"/><path d="M10 38 L13 28 L20 35 Z" fill="#e0a800"/></svg></div><span>INTERVIEW</span></div>
<div class="abs step" style="left:423px"><div class="ring"><svg width="48" height="48" viewBox="0 0 48 48"><path d="M10 38 L13 28 L32 9 L39 16 L20 35 Z" fill="var(--yellow)"/><path d="M10 38 L13 28 L20 35 Z" fill="#e0a800"/></svg></div><span>EXAMS</span></div>
<div class="abs step" style="left:611px"><div class="ring"><svg width="48" height="48" viewBox="0 0 48 48"><path d="M10 38 L13 28 L32 9 L39 16 L20 35 Z" fill="var(--yellow)"/><path d="M10 38 L13 28 L20 35 Z" fill="#e0a800"/></svg></div><span>INTERSHIP</span></div>
<div class="abs step" style="left:799px"><div class="ring"><svg width="48" height="48" viewBox="0 0 48 48"><path d="M10 38 L13 28 L32 9 L39 16 L20 35 Z" fill="var(--yellow)"/><path d="M10 38 L13 28 L20 35 Z" fill="#e0a800"/></svg></div><span>START WORK</span></div>
<div class="abs step" style="left:987px"><div class="ring"><svg width="48" height="48" viewBox="0 0 48 48"><path d="M10 38 L13 28 L32 9 L39 16 L20 35 Z" fill="var(--yellow)"/><path d="M10 38 L13 28 L20 35 Z" fill="#e0a800"/></svg></div><span>FREE SERVICE</span></div>

<section class="abs cta" role="img" aria-label="Photo of a city skyline with a smiling teacher on the right"></section>
<a class="abs btn" style="left:518px;top:2814px;width:157px;height:47px;font-size:13px">APPLY NOW</a>

<footer class="abs footer"></footer>
<div class="abs f-col" style="left:146px;top:2980px;width:170px">
  <h4>OUR MISSION</h4>
  <p>Lorem Ipsum is simply dummy text of the printing and typesetting industry. Lorem Ipsum has been the industry's standard dummy text ever since the 1500s, when an unknown printer took a galley of type and scrambled it to make.</p>
</div>
<div class="abs f-col" style="left:379px;top:2980px">
  <h4>QUICK LINKS</h4>
  <ul><li>Company</li><li>Services</li><li>Solutions</li><li>Resources</li><li>Career</li><li>Contact Us</li></ul>
</div>
<div class="abs f-col" style="left:613px;top:2980px">
  <h4>CONTACT</h4>
  <p>2180 Larkspur Road,<br>Suite 210,<br>Fairhaven, CO 80499</p>
  <p style="margin-top:12px">+1 555 014 2276</p>
  <p style="margin-top:10px">0400 555 182</p>
</div>
<div class="abs f-brand">Bright Lantern Post</div>

<div class="abs base-bar"></div>
<div class="abs" style="left:146px;top:3174px;font-size:11px;color:#888">© 2015 BrightLanternPost.com All rights reserved</div>
<div class="abs social-dots" style="top:3174px;right:100px"><span></span><span></span><span></span></div>

</body>
</html>
```